Support People to improve their image and well-being by provided personalised advise

We need a design for business cards that could be used for production on plano press. We build a new business in our region for advising mostly women (also men though) on style embracing several aspects including fashion, style, self-confidence and ultimately your internal and external image. The business card should be "classy", "french-style". The business is located in the french -speaking part of Switzerland, close to France. The name of the company is Lomu Grace

Target Market(s)

Service fees won't be cheap (medium to premium) thus we target mid-class to upper-class women (1st target) and men (2nd target)

Industry/Entity Type

Life Coaching

Contact Information for Business Card

Conseil en Image

+41 76 418 63 07
tovasel@lomu-grace.example
linkedin.example/in/sel-moran-tova

Logo Text

Lomu Grace

Colors

Designer to choose colors to be used in the design.

```html
<!DOCTYPE html>
<html lang="en">
<head>
<meta charset="utf-8">
<title>Lomu Grace – Business Card</title>
<link rel="stylesheet" href="https://fonts.googleapis.com/css2?family=Lato:wght@400;700&display=swap">
<style>
  :root {
    --backdrop: #9b9b9b;
    --card-white: #ffffff;
    --plum: #731b6e;
    --orchid: #a3179e;
    --ink: #2e2e2e;
    --rule: #e2e2e2;
  }
  html, body {
    margin: 0;
    padding: 0;
    width: 1200px;
    height: 900px;
    overflow: hidden;
    background: var(--backdrop);
    font-family: "Lato", sans-serif;
  }
  .stage {
    position: relative;
    width: 1200px;
    height: 900px;
  }
  .card {
    position: absolute;
    top: 306px;
    width: 439px;
    height: 271px;
    border-radius: 10px;
    overflow: hidden;
  }
  .card-front { left: 149px; background: var(--card-white); }
  .card-back { left: 609px; background: var(--plum); }

  .brand-name {
    position: absolute;
    top: 116px;
    height: 36px;
    font-family: "Lato", sans-serif;
    font-weight: 400;
    font-size: 30px;
    line-height: 36px;
    letter-spacing: 0.5px;
    white-space: nowrap;
    display: flex;
    align-items: center;
    gap: 9px;
  }
  .brand-mark {
    width: 12px;
    height: 12px;
    flex: none;
  }
  .card-front .brand-name {
    left: 27px;
    width: 192px;
    color: var(--plum);
  }
  .card-front .brand-mark { background: var(--orchid); }
  .card-back .brand-name {
    left: 0;
    right: 0;
    justify-content: center;
    color: var(--card-white);
  }
  .card-back .brand-mark { background: var(--card-white); }

  .divider {
    position: absolute;
    left: 234px;
    top: 64px;
    width: 1px;
    height: 142px;
    background: var(--rule);
  }
  .contact {
    position: absolute;
    left: 252px;
    top: 88px;
    color: var(--ink);
  }
  .person-name {
    margin: 0;
    font-weight: 700;
    font-size: 16px;
    color: var(--orchid);
    letter-spacing: 0.2px;
    line-height: 18px;
  }
  .person-role {
    margin: 1px 0 0;
    font-size: 12.5px;
    line-height: 16px;
  }
  .contact-list {
    list-style: none;
    margin: 24px 0 0;
    padding: 0;
    font-size: 12.5px;
    line-height: 16px;
  }
  .contact-list li {
    display: flex;
    align-items: center;
    gap: 6px;
    white-space: nowrap;
  }
  .contact-icon {
    width: 10px;
    height: 10px;
    fill: var(--orchid);
    flex: none;
  }
</style>
</head>
<body>
<main class="stage">
  <section class="card card-front" aria-label="Card front">
    <div class="brand-name"><span class="brand-mark"></span>Lomu Grace</div>
    <div class="divider"></div>
    <div class="contact">
      <p class="person-name">REMY VAUTRIN</p>
      <p class="person-role">Managing Director</p>
      <ul class="contact-list">
        <li>
          <svg class="contact-icon" viewBox="0 0 10 10" aria-hidden="true">
            <path d="M1 4 Q1 2 3 2 L7 2 Q9 2 9 4 L7.5 4.5 L7 3.5 L3 3.5 L2.5 4.5 Z"/>
            <rect x="2" y="5" width="6" height="4" rx="0.8"/>
          </svg>
          +41 76 418 63 07
        </li>
        <li>
          <svg class="contact-icon" viewBox="0 0 10 10" aria-hidden="true">
            <rect x="1" y="2.5" width="8" height="5.5" rx="0.6"/>
            <path d="M1.3 2.9 L5 5.6 L8.7 2.9" fill="none" stroke="#fff" stroke-width="0.8"/>
          </svg>
          tovasel@lomu-grace.example
        </li>
      </ul>
    </div>
  </section>

  <section class="card card-back" aria-label="Card back">
    <div class="brand-name"><span class="brand-mark"></span>Lomu Grace</div>
  </section>
</main>
</body>
</html>
```